Brief 1.
An Overview / Background of the Business & Services-
It is a new business being set up. Our business is to design a solution to enable Alumni of higher institutions in Nigeria apply for their academic transcript through our system. the name of our product will be Record Relay Nigeria. We need logo, site banner, advert banner and several academic images. See www.rrly-ng.example for more insight.
The Target Market / Audience you are trying to reach-
Alumni of Nigeria Universities, usually between the ages of 20-40.
Design Specifics; any preferences or ideas for Style, Colour, Imagery, etc-
Color scheme will be several shades of light blue and white. Please check www.rrly-ng.example for more insight.

Brief 2

Pantrybasket.com is an online food and grocery shop, we supply fresh food stuff and other daily essential needs on request to customers. The site is already up (www.pantrybasket.example). We need logo, site rolling banner, advert banner and several offer graphics as shown in the placeholder images in the site now.
Working women in Nigeria.
Color scheme will be several shades of light Green and White. Please check the site.

```html
<!DOCTYPE html>
<html lang="en">
<head>
<meta charset="utf-8">
<title>Pantrybasket.com – Fresh food online</title>
<link href="https://fonts.googleapis.com/css2?family=Arimo:wght@400;700&family=Archivo+Black&family=Roboto:wght@100;300&display=swap" rel="stylesheet">
<style>
:root{
  --green:#5a9e1e;
  --green-dark:#3f7f10;
  --green-text:#4a8f18;
  --orange:#f26a1a;
  --orange-soft:#f6a75d;
  --grey-line:#d9d9d9;
  --grey-text:#555;
  --nav-grey:#e4e4e4;
  --dark:#2b2b2b;
  --white:#fff;
}
*{box-sizing:border-box;margin:0;padding:0}
html,body{width:818px;height:1200px;overflow:hidden;background:var(--white);font-family:"Arimo",Arial,sans-serif;color:var(--grey-text)}
.page{position:relative;width:818px;height:1200px}
.abs{position:absolute}

/* header */
.brand{left:120px;top:30px;display:flex;align-items:center;gap:9px}
.brand-dot{width:30px;height:30px;border-radius:50%;background:var(--green)}
.brand-name{font-family:"Archivo Black",sans-serif;font-size:19px;color:var(--green);letter-spacing:.3px}
.toplinks{left:354px;top:25px;display:flex;gap:23px;font-size:7.5px;color:var(--grey-text)}
.toplinks .cart{display:flex;align-items:center;gap:4px}
.welcome{left:378px;top:55px;font-size:7.5px;font-style:italic;color:var(--green-dark)}
.search{left:565px;top:51px;width:137px;height:17px;border:1px solid #ccc;font-size:7px;color:#777;padding:4px 7px;display:flex;justify-content:space-between;align-items:center}

.nav{left:118px;top:84px;width:584px;height:27px;background:linear-gradient(#f0f0f0,#d8d8d8);display:flex;font-size:7.5px;color:#444;align-items:center}
.nav span{padding:0 17px}
.nav .active{background:linear-gradient(#555,#222);color:var(--white);height:27px;line-height:27px;padding:0 23px}

.promo{top:119px;height:58px;border:1px solid #ccc;display:flex;align-items:center;gap:18px;padding-left:20px}
.promo-ship{left:118px;width:288px}
.promo-call{left:413px;width:289px}
.promo h2{font-family:"Archivo Black",sans-serif;font-size:18px;color:var(--green);font-weight:400;line-height:1}
.promo p{font-size:8.5px;font-weight:700;color:var(--orange);margin-top:6px}

/* hero */
.hero{left:118px;top:186px;width:402px;height:218px;background:radial-gradient(circle at 55% 40%,#d8202a,#a8141c 45%,#e9e5e0 80%)}
.hero-title{left:146px;top:287px;font-family:"Archivo Black",sans-serif;font-size:15px;color:var(--white);letter-spacing:.5px}
.hero-sub{left:146px;top:306px;font-family:"Roboto",sans-serif;font-weight:300;font-size:27px;color:var(--white)}
.hero-arrows{left:481px;top:384px;display:flex;gap:2px}
.hero-arrows span{width:15px;height:15px;background:rgba(120,120,120,.7);display:block}
.offer-box{left:526px;top:186px;width:176px;height:106px;background:linear-gradient(135deg,#f2a25a,#f7b97a);text-align:center;color:var(--white);padding-top:20px}
.offer-box h3{font-family:"Archivo Black",sans-serif;font-weight:400;font-size:11px;line-height:16px;letter-spacing:.4px}
.offer-box p{font-family:"Roboto",sans-serif;font-weight:300;font-size:11px;margin-top:4px}
.offer-box .btn{display:inline-block;margin-top:9px;background:#ddd;color:#555;font-size:7.5px;padding:6px 20px}
.herbal{left:542px;top:298px;width:160px;height:106px;background:linear-gradient(100deg,#ffffff 35%,#f0dccb 70%,#e8c9ae)}
.herbal-text{left:540px;top:313px;font-family:"Archivo Black",sans-serif;font-size:10px;color:var(--green-dark);line-height:14px}
.herbal-text small{display:block;font-size:7px;color:var(--orange);line-height:11px}

/* section headings */
.heading{font-size:9.5px;color:var(--green-text);font-weight:400;letter-spacing:.2px}
.pager{font-size:8px;color:#999}

/* sidebar */
.cats{left:118px;top:438px;width:137px}
.cats li{list-style:none;height:21px;background:linear-gradient(#f7f7f7,#e7e7e7);border-bottom:1px solid #fff;font-size:7px;color:#444;display:flex;align-items:center;padding:0 8px;justify-content:space-between}
.cats li span::before{content:"›";margin-right:6px;color:#666}
.cats .plus{width:7px;height:7px;border:1px solid #999;font-size:6px;line-height:5px;text-align:center;color:#666}
.hurry{left:118px;top:578px;width:137px;height:219px;background:linear-gradient(#2a0f12 45%,#8a1a2e 75%,#e06080);text-align:center;padding-top:24px}
.hurry h3{font-family:"Archivo Black",sans-serif;font-weight:400;font-size:12px;color:var(--orange);line-height:15px}
.hurry .big{font-family:"Archivo Black",sans-serif;font-size:30px;color:#f7d21c;margin-top:6px}
.hurry .big small{font-size:9px;color:var(--white)}
.special{left:118px;top:813px;width:137px;height:165px;border:1px solid #ccc;padding:12px 11px}
.special .img{width:112px;height:80px;margin:10px auto 0;background:radial-gradient(circle,#2f7d1c 30%,#e6a02a 55%,#fff 75%)}
.special .name{font-size:9px;color:var(--green-text);margin-top:10px}
.special .row{display:flex;justify-content:space-between;align-items:center;margin-top:7px;font-size:9px;color:var(--green-dark)}
.special .buy{background:var(--orange);color:var(--white);font-size:6.5px;padding:6px 11px}

/* products */
.grid{left:282px;width:420px;display:grid;grid-template-columns:repeat(3,128px);column-gap:18px}
.card{height:160px;border:1px solid #ccc;text-align:center;position:relative}
.card .img{height:95px;margin:8px 6px 0}
.card .title{font-size:9px;color:var(--green-text);margin-top:12px}
.card .row{display:flex;justify-content:space-between;align-items:center;padding:0 12px;margin-top:8px;font-size:9px;color:var(--green-dark)}
.card .add{border:1px solid #aaa;background:linear-gradient(#fafafa,#ddd);font-size:5.5px;font-weight:700;color:#555;padding:3px 8px}
.card.active .foot{position:absolute;left:-1px;right:-1px;bottom:-4px;height:53px;background:var(--green);padding-top:9px}
.card.active .title,.card.active .row{color:var(--white);margin-top:0}
.card.active .row{margin-top:10px}

/* footer */
.footer{left:0;top:1012px;width:818px;height:188px;background:linear-gradient(#e9e9e9,#fff 30px)}
.foot-brand{left:125px;top:1040px;text-align:center;width:96px}
.foot-brand .dot{width:30px;height:30px;border-radius:50%;background:var(--green);margin:0 auto 14px}
.foot-brand .name{font-family:"Archivo Black",sans-serif;font-size:12px;color:var(--green)}
.col h4{font-size:8px;color:var(--green-text);font-weight:700;margin-bottom:9px}
.col li{list-style:none;font-size:6.5px;color:#666;line-height:16.5px}
.social li{display:flex;align-items:center;gap:4px;line-height:30px}
.social .ico{width:18px;height:18px;border-radius:50%;background:#666}
.payments{display:flex;gap:4px;border:1px solid #ccc;background:#f3f3f3;padding:5px 6px}
.payments span{width:28px;height:15px;border:1px solid #bbb;background:var(--white)}
.payments span:nth-child(2){background:#2e7bbf}
.payments span:nth-child(3){background:#e65a3a}
.payments span:nth-child(4){width:40px}
.rule{left:118px;top:1142px;width:584px;height:1px;background:#ddd}
.copy{left:0;top:1159px;width:818px;text-align:center;font-size:6.5px;color:#666}
</style>
</head>
<body>
<div class="page">

  <div class="abs brand"><span class="brand-dot"></span><span class="brand-name">PANTRYBASKET</span></div>
  <div class="abs toplinks"><span>My Account</span><span>My Wishlist</span><span>My Cart</span><span>Checkout</span><span>Log In</span>
    <span class="cart"><svg width="9" height="8" viewBox="0 0 9 8"><path d="M0 1h2l1 4h5l1-3H2.5" fill="none" stroke="#666" stroke-width=".8"/><circle cx="3.5" cy="7" r=".7" fill="#666"/><circle cx="7.5" cy="7" r=".7" fill="#666"/></svg>Your cart is : 0 items</span></div>
  <div class="abs welcome">Welcome to Pantrybasket.com. Feed well, live well</div>
  <div class="abs search"><span>Search :</span><svg width="9" height="9" viewBox="0 0 9 9"><circle cx="3.7" cy="3.7" r="2.8" fill="none" stroke="#888"/><path d="M5.8 5.8 8.5 8.5" stroke="#888"/></svg></div>

  <nav class="abs nav"><span class="active">HOME</span><span>HEALTH &amp; WELLNESS</span><span>FRUITS &amp; VEGS</span><span>POULTRY, MEAT &amp; FISH</span><span>FOOD STUFFS</span><span>RECIPES</span><span>OTHERS</span></nav>

  <div class="abs promo promo-ship">
    <svg width="46" height="30" viewBox="0 0 46 30"><rect x="14" y="2" width="30" height="20" fill="#888"/><path d="M2 10h11v12H2zM4 11h7v5H4z" fill="#999"/><circle cx="9" cy="24" r="4" fill="#777" stroke="#fff" stroke-width="1.5"/><circle cx="35" cy="24" r="4" fill="#777" stroke="#fff" stroke-width="1.5"/></svg>
    <div><h2>FREE SHIPPING</h2><p>ON ORDER OVER $30 OFFER TODAY</p></div>
  </div>
  <div class="abs promo promo-call">
    <svg width="40" height="40" viewBox="0 0 40 40"><circle cx="20" cy="20" r="18" fill="none" stroke="#777" stroke-width="2.5"/><path d="M14 11c-2 2-2 6 2 11s8 8 11 7l2-3-4-3-2 2c-2-1-5-4-6-6l2-2-3-4z" fill="#777"/></svg>
    <div><h2>GIVE US CALL</h2><p>1-800 PANTRY (1-800-726-879)</p></div>
  </div>

  <div class="abs hero" role="img" aria-label="Bowl of fresh strawberries"></div>
  <div class="abs hero-title">FRUITS &amp; VEGS</div>
  <div class="abs hero-sub">SHOP ONLINE NOW</div>
  <div class="abs hero-arrows"><span></span><span></span></div>
  <div class="abs offer-box"><h3>FREE DELIVERY &amp;<br>GET 10% DISCOUNT</h3><p>on every Registered Users</p><span class="btn">READ MORE</span></div>
  <div class="abs herbal" role="img" aria-label="Spa and skin care scene"></div>
  <div class="abs herbal-text">HERBAL &amp;<br><span style="color:#222">AYURVEDIC</span><small>&amp; SPA PRODUCTS</small></div>

  <div class="abs heading" style="left:118px;top:420px">CATEGORIES</div>
  <ul class="abs cats">
    <li><span>Health &amp; Wellness</span></li>
    <li><span>Fruits &amp; Vegs</span><i class="plus">+</i></li>
    <li><span>Poultry, Meat &amp; Fish</span><i class="plus">+</i></li>
    <li><span>Food Stuffs</span><i class="plus">+</i></li>
    <li><span>Recipes</span></li>
    <li><span>Others</span><i class="plus">+</i></li>
  </ul>
  <div class="abs hurry" role="img" aria-label="Strawberries splashing in cream"><h3>HURRY OFFER<br>ENDS SOON</h3><div class="big">50%<small>OFFER</small></div></div>

  <div class="abs special">
    <div class="heading" style="display:flex;justify-content:space-between">SPECIAL PRODUCTS<span class="pager">‹ ›</span></div>
    <div class="img" role="img" aria-label="Green, red and yellow bell peppers"></div>
    <div class="name">CUM SOCIIS</div>
    <div class="row"><span>130.00</span><span class="buy">ADD TO CART</span></div>
  </div>

  <div class="abs heading" style="left:282px;top:420px">LATEST PRODUCTS</div>
  <div class="abs pager" style="left:686px;top:419px">‹ ›</div>
  <div class="abs grid" style="top:441px">
    <div class="card active"><div class="img" role="img" aria-label="Whole fish" style="background:radial-gradient(ellipse 45% 18%,#8a8270,#fff)"></div><div class="foot"><div class="title">TILAPIA FISH (1KG)</div><div class="row"><span>1,000.00</span><span class="add">ADD TO CART</span></div></div></div>
    <div class="card"><div class="img" role="img" aria-label="Pasta, vegetables and oil" style="background:radial-gradient(circle,#e2c040 20%,#6aa030 45%,#fff 70%)"></div><div class="title">TILAPIA FISH (1KG)</div><div class="row"><span>1,000.00</span><span class="add">ADD TO CART</span></div></div>
    <div class="card"><div class="img" role="img" aria-label="Sacks of nuts and vegetables" style="background:radial-gradient(circle,#b07a45 25%,#d8b98e 50%,#fff 75%)"></div><div class="title">TILAPIA FISH (1KG)</div><div class="row"><span>1,000.00</span><span class="add">ADD TO CART</span></div></div>
  </div>

  <div class="abs heading" style="left:282px;top:621px">FEATURED PRODUCTS</div>
  <div class="abs pager" style="left:686px;top:620px">‹ ›</div>
  <div class="abs grid" style="top:642px">
    <div class="card"><div class="img" role="img" aria-label="Whole fish" style="background:radial-gradient(ellipse 45% 14%,#9a9a90,#fff)"></div><div class="title">TILAPIA FISH (1KG)</div><div class="row"><span>1,000.00</span><span class="add">ADD TO CART</span></div></div>
    <div class="card"><div class="img" role="img" aria-label="Fresh peaches" style="background:radial-gradient(circle,#f0a030 20%,#d83a20 45%,#fff 70%)"></div><div class="title">TILAPIA FISH (1KG)</div><div class="row"><span>1,000.00</span><span class="add">ADD TO CART</span></div></div>
    <div class="card"><div class="img" role="img" aria-label="Tilapia fish" style="background:radial-gradient(ellipse 45% 25%,#5a6a70,#fff)"></div><div class="title">TILAPIA FISH (1KG)</div><div class="row"><span>1,000.00</span><span class="add">ADD TO CART</span></div></div>
  </div>
  <div class="abs grid" style="top:817px">
    <div class="card"><div class="img" role="img" aria-label="Ripe tomatoes" style="background:radial-gradient(circle,#e83a20 35%,#fff 70%)"></div><div class="title">TILAPIA FISH (1KG)</div><div class="row"><span>1,000.00</span><span class="add">ADD TO CART</span></div></div>
    <div class="card"><div class="img" role="img" aria-label="Green pea pods" style="background:linear-gradient(160deg,#8ec63c,#5a9e1e 60%,#f4f4f4)"></div><div class="title">TILAPIA FISH (1KG)</div><div class="row"><span>1,000.00</span><span class="add">ADD TO CART</span></div></div>
    <div class="card"><div class="img" role="img" aria-label="Grocery bag with fruit and vegetables" style="background:radial-gradient(circle,#c8a478 25%,#d85030 45%,#6aa030 60%,#fff 78%)"></div><div class="title">TILAPIA FISH (1KG)</div><div class="row"><span>1,000.00</span><span class="add">ADD TO CART</span></div></div>
  </div>

  <div class="abs footer"></div>
  <div class="abs foot-brand"><div class="dot"></div><div class="name">PANTRYBASKET</div></div>
  <div class="abs col" style="left:246px;top:1036px"><h4>CUSTOMER SERVICE</h4><ul><li>About Us</li><li>Delivery Information</li><li>Privacy Policy</li><li>Term &amp; Condition</li></ul></div>
  <div class="abs col" style="left:369px;top:1036px"><h4>MY ACCOUNT</h4><ul><li>My Product</li><li>My Orders</li><li>My Address</li><li>My Personal Info</li></ul></div>
  <div class="abs col social" style="left:469px;top:1036px"><h4>FOLLOW US</h4><ul><li><span class="ico"></span>: Friends Page</li><li><span class="ico"></span>: Short Posts</li></ul></div>
  <div class="abs col" style="left:561px;top:1037px"><h4>PAYMENT OPTIONS</h4><div class="payments"><span></span><span></span><span></span><span></span></div></div>
  <div class="abs rule"></div>
  <div class="abs copy">© 2014 Pantry Basket. All Rights Reserved.</div>
</div>
</body>
</html>
```